4 x Florist Footpath Signage Boards that are consistant with each other for a modern florist

Eye catching, easy to read. little bit floral.
See example attached for wording. We are a modern florist in a country town.
This will be out on the street and needs to stand out!!

The Signage Panels
1. Valentines Day - 14th Feb
2. Workshop Signage boards - see attached example
3. Mothers Day Signage Board - 'Treat mum this Mothers Day'
4. We Are Open

Attached is a copy of the design guidelines and the template. the base of the sign is white.

Target Market(s)

Modern

Industry/Entity Type

Florist

Font styles to use
Sans Serif

Colors
eea4c8
f59296
ffffff
757575

Requirements
Must have
• flowers
• weddings
• giftware
• workshops
• flowers make people happy
• lucywrenblooms.co.nz
Nice to have
• Logo
• little bit of floral or greenery
• my shop is modem and industrial
Should not have
• Needs to be able to read easy

```html
<!DOCTYPE html>
<html lang="en">
<head>
<meta charset="utf-8">
<title>Lucy Wren Blooms – Mothers Day Footpath Board</title>
<link rel="stylesheet" href="https://fonts.googleapis.com/css2?family=Cuprum:wght@400;500&display=swap">
<style>
  :root {
    --board-white: #ffffff;
    --outline-grey: #757575;
    --brand-gold: #c4a14c;
    --band-pink: #ee8cee;
    --band-olive: #b3a222;
    --text-white: #ffffff;
    --leaf-dark: #2f4a2c;
    --leaf-mid: #5d7d48;
    --bloom-pink: #d23fb4;
  }
  html, body {
    margin: 0;
    padding: 0;
    overflow: hidden;
    background: var(--board-white);
  }
  .board {
    position: relative;
    width: 904px;
    height: 1200px;
    overflow: hidden;
    background: var(--board-white);
    font-family: "Cuprum", "Arial Narrow", sans-serif;
  }
  .board-photo {
    position: absolute;
    left: 500px;
    top: 0;
    width: 404px;
    height: 1200px;
    background:
      radial-gradient(ellipse 240px 160px at 60% 92%, rgba(210, 63, 180, 0.85), transparent 70%),
      radial-gradient(ellipse 180px 200px at 75% 40%, rgba(230, 200, 185, 0.75), transparent 70%),
      radial-gradient(ellipse 160px 220px at 20% 55%, rgba(200, 170, 160, 0.6), transparent 70%),
      linear-gradient(180deg, #3a4a3a 0%, var(--leaf-mid) 35%, var(--leaf-dark) 70%, #4a6a3c 100%);
  }
  .board-outline {
    position: absolute;
    inset: 0;
    pointer-events: none;
  }
  .brand-name {
    position: absolute;
    left: 134px;
    top: 272px;
    width: 280px;
    text-align: center;
    color: var(--brand-gold);
    font-weight: 400;
    font-size: 27px;
    line-height: 40px;
    letter-spacing: 5px;
    text-transform: uppercase;
  }
  .headline-band {
    position: absolute;
    display: flex;
    align-items: center;
    justify-content: center;
    color: var(--text-white);
    font-weight: 500;
    line-height: 1;
    white-space: nowrap;
  }
  .headline-band--pink {
    left: 112px;
    top: 610px;
    width: 574px;
    height: 120px;
    background: var(--band-pink);
    font-size: 112px;
  }
  .headline-band--olive {
    left: 44px;
    top: 746px;
    width: 816px;
    height: 124px;
    background: var(--band-olive);
    font-size: 108px;
  }
</style>
</head>
<body>
  <main class="board">
    <div class="board-photo" role="img" aria-label="Photo of a mother and young daughter browsing plants in a garden nursery, with pink bougainvillea in the foreground"></div>

    <svg class="board-outline" width="904" height="1200" viewBox="0 0 904 1200" aria-hidden="true">
      <path d="M8 1192 V1064 L26 1046 V60 Q26 10 76 10 H900" fill="none" stroke="var(--outline-grey)" stroke-width="2"/>
      <rect x="380" y="50" width="140" height="34" rx="17" fill="var(--board-white)" stroke="var(--outline-grey)" stroke-width="2"/>
    </svg>

    <div class="brand-name">Lucy Wren<br>Blooms</div>

    <h1 class="headline-band headline-band--pink" style="margin:0">Treat mum</h1>
    <p class="headline-band headline-band--olive" style="margin:0">this Mothers Day</p>
  </main>
</body>
</html>
```